RW Framewell Inc Business cards

We need business cards using our existing logo but slightly modified. Right now the logo says RW Loadbearing Masonry. We want to keep the RW part of the design, but replace the Structural Concrete portion with "FRAMEWELL". Please see the attached file.
Ideally this would be a blank template so we can add Different Names, titles, and phone numbers later.
On the one side we want only the logo and on the other side the detail. I'm attaching an example for you to see.
Please reach out with any other questions. Our address and other details will be given out once we find a design we like.

Target Market(s)

Construction Industry

```html
<!DOCTYPE html>
<html lang="en">
<head>
<meta charset="utf-8">
<title>RW Framewell Inc — Business Cards</title>
<link href="https://fonts.googleapis.com/css2?family=Montserrat:wght@600;700&family=Roboto:wght@400;500&display=swap" rel="stylesheet">
<style>
  :root {
    --backdrop: #3b3b3d;
    --card-dark: #1f1f21;
    --brand-blue: #2f63a6;
    --stripe-grey: #6b6b6d;
    --white: #ffffff;
    --name-blue: #3a6fb4;
  }
  * { box-sizing: border-box; margin: 0; padding: 0; }
  html, body { width: 799px; height: 1200px; overflow: hidden; }
  body {
    background: var(--backdrop);
    display: flex;
    flex-direction: column;
    align-items: center;
    justify-content: space-around;
    padding: 90px 0;
    font-family: "Roboto", Arial, sans-serif;
  }
  .card {
    width: 620px;
    height: 354px;
    border-radius: 4px;
    position: relative;
    overflow: hidden;
    box-shadow: 0 14px 30px rgba(0,0,0,.45);
  }
  .card-front {
    background: var(--card-dark);
    display: flex;
    align-items: center;
    justify-content: center;
  }
  .wordmark {
    display: flex;
    align-items: center;
    gap: 16px;
    font-family: "Montserrat", Arial, sans-serif;
    font-weight: 700;
    color: var(--white);
    letter-spacing: 6px;
  }
  .wordmark-square {
    width: 34px;
    height: 34px;
    background: var(--brand-blue);
  }
  .card-front .wordmark { font-size: 40px; }

  .card-back { background: var(--brand-blue); }
  .back-header {
    position: absolute;
    inset: 0 0 auto 0;
    height: 104px;
    background: var(--card-dark);
    border-bottom: 9px solid var(--stripe-grey);
    padding: 26px 30px;
  }
  .holder-name {
    font-family: "Montserrat", Arial, sans-serif;
    font-weight: 600;
    font-size: 20px;
    color: var(--name-blue);
  }
  .holder-title {
    font-size: 13px;
    color: var(--white);
    margin-top: 3px;
  }
  .contact {
    position: absolute;
    left: 30px;
    top: 140px;
    color: var(--white);
    font-size: 15px;
    line-height: 1.45;
  }
  .contact-address { margin-left: 26px; margin-bottom: 6px; }
  .contact-row { display: flex; align-items: center; gap: 10px; }
  .contact-row svg { width: 15px; height: 15px; flex: none; }
  .card-back .wordmark {
    position: absolute;
    right: 34px;
    bottom: 60px;
    font-size: 30px;
    letter-spacing: 5px;
  }
  .card-back .wordmark-square { width: 26px; height: 26px; background: var(--white); }
</style>
</head>
<body>
  <section class="card card-front">
    <div class="wordmark"><span class="wordmark-square"></span>RW FRAMEWELL</div>
  </section>

  <section class="card card-back">
    <header class="back-header">
      <p class="holder-name">Daniel RW Hart</p>
      <p class="holder-title">Managing Director</p>
    </header>
    <div class="contact">
      <p class="contact-address">57 Ridgeline Ave., Millbrook,<br>California, US 95810</p>
      <p class="contact-row">
        <svg viewBox="0 0 16 16" aria-hidden="true"><path fill="#fff" d="M3.5 1.5l2.5 0 1 3.5-1.6 1.2a8 8 0 0 0 4.4 4.4L11 9l3.5 1v2.5c0 1-1 2-2 2A11 11 0 0 1 1.5 3.5c0-1 1-2 2-2z"/></svg>
        530-555-0142
      </p>
      <p class="contact-row">
        <svg viewBox="0 0 16 16" aria-hidden="true"><rect x="1.5" y="3.5" width="13" height="9" fill="none" stroke="#fff" stroke-width="1.5"/><path d="M1.5 3.5L8 9l6.5-5.5" fill="none" stroke="#fff" stroke-width="1.5"/></svg>
        daniel@framewellbuild.com
      </p>
      <p class="contact-row">
        <svg viewBox="0 0 16 16" aria-hidden="true"><circle cx="8" cy="8" r="6.3" fill="none" stroke="#fff" stroke-width="1.4"/><ellipse cx="8" cy="8" rx="2.8" ry="6.3" fill="none" stroke="#fff" stroke-width="1.2"/><path d="M1.7 8h12.6" stroke="#fff" stroke-width="1.2"/></svg>
        www.framewellbuild.com
      </p>
    </div>
    <div class="wordmark"><span class="wordmark-square"></span>RW FRAMEWELL</div>
  </section>
</body>
</html>
```